Kelumo.cn needs pages to be re-designed

www.kelumo.cn is our current new site which was launched in April.
We're a financial services website in the crowdfunding space in China to connect borrower's and lender's.

test.kelumo.cn is our test site
u: test
p: newtest
http://test.kelumo.cn/
http://test.kelumo.cn/user/accounts/new_lender
http://test.kelumo.cn/user/accounts/new_borrower
http://test.kelumo.cn/introductions/protection
http://test.kelumo.cn/introductions
http://test.kelumo.cn/introductions/kelumo_admin
http://test.kelumo.cn/introductions/contact
Some of the pages have pop-ups in the bloc's of the pages. Please click the links, to see more content.

User's currently criticize the website for being:
- Too Western looking
- Too simple, too little content
- Content NOT in the pop-ups are too simple
- Pictures are too big and too much blank space
- Relevant information is not there when needed
- The pictures are too generic

What we would like to do is re-design those pages with the same color scheme and style to be more compelling, efficient, non-intimidating and easy-to-use. Our audience is Ages 25-35 predominantly male investors.
We are looking for more ideas to make the content match the style, while bridging western and chinese design. Our ultimate goal is to increase registrants to the website and highlight our core competitive advantages.

Some competitors websites are:
www.fobuxiqi.com
www.tamev.com
www.zzzlendo.com

Reason: Not enough good designs that follow the prompt. Same style, better information layout!

Reason: Still have not received a design we're satisfied with

Reason: WE DONT WANT A COMPLETE REDESIGN OF PAGES . KEEP THE EXACT SAME COLOR AND STYLE - WE WANT CONTENT RE-DESIGN! THE BLOCS ARE TOO SIMPLE - WE WANT MORE CONTENT INSIDE.

Reason: no new designs

Reason: no new designs

Reason: other non-registered pages need to be re-designed

```html
<!DOCTYPE html>
<html lang="zh-CN">
<head>
<meta charset="utf-8">
<title>可路贷 - 合作伙伴</title>
<link href="https://fonts.googleapis.com/css2?family=Noto+Sans+SC:wght@400;500;700&display=swap" rel="stylesheet">
<style>
:root{
  --green:#5fae1e;
  --ink:#333;
  --text:#666;
  --muted:#999;
  --shape:#bdbdbd;
  --row-alt:#f2f2f2;
  --tab-bg:#3d3d3d;
  --footer:#3a3a3a;
  --footer-text:#cfcfcf;
  --badge:#4a92d6;
  --panel:#e9e9e9;
  --panel-alt:#f3f3f3;
  --pill:#5a5a5a;
}
*{margin:0;padding:0;box-sizing:border-box}
html,body{width:1200px;height:3256px;overflow:hidden}
body{font-family:"Noto Sans SC",sans-serif;color:var(--ink);background:#fff;position:relative}
.site-header{height:88px;display:flex;align-items:center;justify-content:space-between;padding:0 100px}
.brand{display:flex;align-items:center;gap:12px;font-size:26px;font-weight:700;color:var(--green)}
.brand-dot{width:46px;height:46px;border-radius:50%;background:var(--green)}
.top-nav{display:flex;gap:40px;font-size:15px;color:var(--ink)}
.top-nav span{display:flex;align-items:center;gap:8px}
.top-nav svg{width:16px;height:16px}
.hero{position:relative;height:482px;background:linear-gradient(180deg,#9a9a98 0%,#6f6a66 45%,#4f4b48 100%)}
.hero-title{position:absolute;left:0;right:0;top:402px;text-align:center;color:#fff;font-size:36px;font-weight:500;letter-spacing:3px}
.hero-dots{position:absolute;right:120px;top:20px;display:flex;gap:8px}
.hero-dots i{width:10px;height:10px;border-radius:50%;background:rgba(255,255,255,.5)}
.hero-dots i:first-child{background:#fff}
.tab-bar{height:58px;background:var(--tab-bg);display:flex;padding-left:84px}
.tab-bar a{width:205px;display:flex;align-items:center;justify-content:center;color:#fff;font-size:22px;text-decoration:none}
.tab-bar a.active{background:var(--green)}
.section-title{padding:50px 0 0 128px;height:112px;font-size:22px;color:var(--green);font-weight:500}
.partner{display:flex;align-items:center;padding:0 60px 0 128px}
.partner.alt{background:var(--row-alt)}
.partner-mark{width:200px;display:flex;flex-direction:column;gap:14px}
.logo{display:flex;align-items:center;gap:8px;font-weight:500;font-size:15px;color:var(--ink)}
.logo i{width:20px;height:20px;flex:none;background:var(--shape)}
.logo i.c{border-radius:50%}
.badge{background:var(--badge);color:#fff;font-size:14px;font-weight:700;padding:6px 10px;width:186px}
.partner-body{margin-left:70px;flex:1}
.partner-body h3{font-size:14px;font-weight:700;color:var(--ink);margin-bottom:10px}
.partner-body p{font-size:11px;line-height:18px;color:var(--text)}
.more-btn{display:inline-block;margin-top:14px;background:var(--green);color:#fff;font-size:12px;padding:4px 22px;border-radius:12px}
.news{display:flex;height:256px;background:var(--panel)}
.news-col{flex:1;padding:34px 0 0 204px}
.news-col.right{background:var(--panel-alt);padding-left:44px}
.news-col h2{font-size:24px;color:var(--green);font-weight:500;margin-bottom:10px}
.news-col ul{list-style:none;font-size:11px;color:var(--ink);line-height:24px}
.news-col li::before{content:"";display:inline-block;width:6px;height:6px;background:var(--ink);margin-right:12px;vertical-align:middle}
.news-col li.hl{color:var(--green);text-decoration:underline}
.news-col li.hl::before{background:var(--green)}
.pill{display:inline-block;margin-top:10px;background:var(--pill);color:#fff;font-size:12px;padding:4px 22px;border-radius:12px}
.strip{height:81px;padding:12px 0 0 208px}
.strip h4{font-size:13px;font-weight:500;margin-bottom:8px}
.strip-logos{display:flex;gap:26px;align-items:center;font-size:13px;font-weight:500;color:var(--ink)}
.site-footer{height:182px;background:var(--footer);color:var(--footer-text);position:relative;padding:22px 0 0 174px;font-size:13px}
.site-footer .row{display:flex;gap:16px;margin-bottom:14px;align-items:center}
.social{width:22px;height:22px;border-radius:50%;background:#777}
.service-btn{border:1px solid #888;border-radius:14px;padding:3px 18px;color:#fff}
.hotline{position:absolute;right:150px;top:18px;text-align:center;color:#fff}
.hotline small{display:block;font-size:13px;color:var(--footer-text)}
.hotline strong{display:block;font-size:30px;font-weight:700;margin:6px 0 2px}
.hotline em{font-style:normal;font-size:10px;color:var(--footer-text)}
.certs{position:absolute;left:264px;top:142px;display:flex;gap:28px}
.certs i{width:96px;height:28px;background:#ececec;border-radius:2px}
.copyright{height:51px;display:flex;align-items:center;justify-content:space-between;padding:0 100px 0 174px;font-size:11px;color:var(--muted)}
.copyright .brand{font-size:18px;gap:8px}
.copyright .brand-dot{width:26px;height:26px}
</style>
</head>
<body>
<header class="site-header">
  <div class="brand"><span class="brand-dot"></span>可路贷 <span style="font-size:13px">Kelumo.cn</span></div>
  <nav class="top-nav">
    <span><svg viewBox="0 0 16 16"><path d="M8 1l6 2.5v4C14 11 11 14 8 15 5 14 2 11 2 7.5v-4z" fill="#555"/></svg>安全</span>
    <span><svg viewBox="0 0 16 16"><circle cx="8" cy="8" r="7" fill="#555"/></svg>投资</span>
    <span><svg viewBox="0 0 16 16"><rect x="3" y="1" width="10" height="14" fill="#555"/></svg>贷款</span>
    <span><svg viewBox="0 0 16 16"><rect x="3" y="7" width="10" height="8" fill="#555"/><path d="M5 7V5a3 3 0 016 0v2" stroke="#555" stroke-width="2" fill="none"/></svg>登录 ▾</span>
  </nav>
</header>

<section class="hero" role="img" aria-label="团队成员的手叠放在一起，象征合作的照片">
  <div class="hero-dots"><i></i><i></i><i></i><i></i></div>
  <h1 class="hero-title">我們的合作夥伴</h1>
</section>

<nav class="tab-bar">
  <a>公司介绍</a><a>公司管理</a><a class="active">合作伙伴</a><a>加入我们</a><a>联系我们</a>
</nav>

<h2 class="section-title">合作伙伴</h2>

<main class="partners">
  <article class="partner" style="height:197px">
    <div class="partner-mark"><div class="logo"><i class="c"></i>华泰安康</div><div class="badge">资产管理规模:超370亿</div></div>
    <div class="partner-body"><h3>华泰安康保险股份有限公司</h3><p>华泰安康保险股份有限公司是国内大型综合保险集团，总部位于北京，注册资本雄厚，在全国设有数千家分支机构。公司品牌价值领先，多年入选行业权威榜单，为客户提供寿险、养老、健康等全方位保障服务，坚持稳健经营与专业服务并重。</p><span class="more-btn">了解更多</span></div>
  </article>
  <article class="partner" style="height:179px">
    <div class="partner-mark"><div class="logo">Hensard 恒德</div><div class="badge">资产管理规模:超100亿</div></div>
    <div class="partner-body"><h3>恒德(北京)保险经纪有限公司</h3><p>恒德(北京)保险经纪有限公司是全国性保险经纪机构，拥有专业的风险管理与理赔服务团队，为企业与个人客户设计保险方案，提供风险评估、保单管理及理赔协助等一站式服务，致力于成为客户信赖的长期伙伴。</p><span class="more-btn">了解更多</span></div>
  </article>
  <article class="partner alt" style="height:116px">
    <div class="partner-mark"><div class="logo"><i></i>Veronel Asia Direct</div></div>
    <div class="partner-body"><h3>Veronel Asia Direct</h3><p>Veronel Asia Direct是Veronel Capital Markets亚洲区分公司，以合规稳健的投资管理著称，Veronel Capital Markets隶属于Bank Veronel集团。</p></div>
  </article>
  <article class="partner" style="height:110px">
    <div class="partner-mark"><div class="logo">Octavra</div></div>
    <div class="partner-body"><h3>Octavra</h3><p>Octavra 是一家早期风险投资机构，专注于高科技与互联网领域，覆盖金融、大数据等行业投资。</p></div>
  </article>
  <article class="partner alt" style="height:120px">
    <div class="partner-mark"><div class="logo"><i></i>中华微贷协会</div></div>
    <div class="partner-body"><h3>中华微贷协会</h3><p>中华微贷协会（英文名称：Sino Microlending Association）是全国性行业组织，致力于推动小额信贷行业规范健康发展。</p></div>
  </article>
  <article class="partner" style="height:170px">
    <div class="partner-mark"><div class="logo"><i class="c"></i>微贷服务中介机构协作会</div></div>
    <div class="partner-body"><h3>微贷服务中介机构协作会</h3><p>微贷服务中介机构协作会是由多家中介服务机构共同发起的行业自律组织，倡导诚信经营、信息透明和风险可控，推动会员间的数据共享与合作，保护借贷双方的合法权益，促进微贷服务行业的健康发展与规范运营，为普惠金融提供有力支持。</p></div>
  </article>
  <article class="partner alt" style="height:126px">
    <div class="partner-mark"><div class="logo"><i></i>融安信达</div></div>
    <div class="partner-body"><h3>北京融安信达征信有限公司</h3><p>北京融安信达征信有限公司成立于2012年，是从事信用信息服务、评估、信息咨询的专业机构，为会员提供共享服务。</p></div>
  </article>
  <article class="partner" style="height:136px">
    <div class="partner-mark"><div class="logo"><i class="c"></i>上海诚信数据</div></div>
    <div class="partner-body"><h3>上海诚信数据有限公司</h3><p>上海诚信数据有限公司成立于1999年，是国内较早从事个人与企业信用信息服务的专业机构，具有丰富的数据积累与风控经验，为金融机构提供征信查询和评估服务。</p></div>
  </article>
  <article class="partner alt" style="height:116px">
    <div class="partner-mark"><div class="logo"><i></i>大衡律师事务所</div></div>
    <div class="partner-body"><h3>大衡律师事务所</h3><p>大衡律师事务所成立于1992年，是国内规模较大的综合性律师事务所之一。</p></div>
  </article>
  <article class="partner" style="height:136px">
    <div class="partner-mark"><div class="logo">SkyNodeCloud</div></div>
    <div class="partner-body"><h3>云岭科技</h3><p>云岭科技是领先的云端服务器运维管理服务商，为互联网企业提供高可用的托管、监控与安全服务，帮助客户降低成本、提升系统稳定性。</p></div>
  </article>
  <article class="partner alt" style="height:138px">
    <div class="partner-mark"><div class="logo"><i class="c"></i>政信通</div></div>
    <div class="partner-body"><h3>北京政信通科技有限公司</h3><p>北京政信通科技有限公司成立于2001年，是国内领先的身份信息核查服务提供商，为金融、电信、电商等行业提供实名认证与反欺诈服务，业务覆盖全国。</p></div>
  </article>
  <article class="partner" style="height:128px">
    <div class="partner-mark"><div class="logo"><i class="c"></i>易付通</div></div>
    <div class="partner-body"><h3>易付通</h3><p>易付通（EasyPayo）是专业的第三方支付平台，成立于2003年，总部位于北京，为商户与个人用户提供安全便捷的在线支付、代收付与资金结算服务。</p></div>
  </article>
  <article class="partner alt" style="height:128px">
    <div class="partner-mark"><div class="logo"><i class="c"></i>国汇宝</div></div>
    <div class="partner-body"><h3>国汇宝</h3><p>国汇宝是专业的在线支付服务平台，针对中小企业与电子商务需求，提供便捷安全的资金收付与账户管理服务。</p></div>
  </article>
  <article class="partner" style="height:150px">
    <div class="partner-mark"><div class="logo"><i></i>北京网络商务协会</div></div>
    <div class="partner-body"><h3>北京网络商务协会</h3><p>北京网络商务协会成立于2002年，是由首都网络商务领域企业自愿组成的行业组织，会员涵盖电商、支付、物流、软件等多个领域，致力于推动行业诚信建设与健康发展。</p></div>
  </article>
</main>

<section class="news">
  <div class="news-col">
    <h2>媒体报道</h2>
    <ul>
      <li class="hl">这就是为什么人们想一个简单的例子</li>
      <li>这就是为什么人们想</li>
      <li>这就是为什么人们想一个简单的例子</li>
      <li>这就是为什么人们想一个简单的例子</li>
      <li>这就是为什么人们想一个简单的例子</li>
    </ul>
    <span class="pill">更多&gt;</span>
  </div>
  <div class="news-col right">
    <h2>官方公告</h2>
    <ul>
      <li>这就是为什么一个简单的例子</li>
      <li>这就是为什么人们想一个简单的例子</li>
      <li>这就是为什么人们想一个简单的例子</li>
      <li>这就是为什么人们想</li>
      <li>这就是为什么人们想一个简单的例子</li>
    </ul>
    <span class="pill">更多&gt;</span>
  </div>
</section>

<section class="strip">
  <h4>合作伙伴</h4>
  <div class="strip-logos">
    <span>Veronel Asia Direct</span>
    <span>SkyNodeCloud</span>
    <span>中华微贷协会</span>
    <span>Octavra</span>
    <span>融安信达</span>
    <span>上海诚信数据</span>
  </div>
</section>

<footer class="site-footer">
  <div class="row">投资 <span>贷款</span><span>安全</span><span>媒体</span><span>合作</span><span>关于我们</span><span>联系我们</span><span>加入我们</span><span>帮助中心</span></div>
  <div class="row">友情链接：借贷之窗 <span>贷眼观察</span><span>信贷俱乐部</span></div>
  <div class="row">客户服务：<i class="social"></i><i class="social"></i><i class="social"></i><i class="social"></i><span class="service-btn">在线客服</span></div>
  <div class="hotline"><small>客服电话</small><strong>400-820-5176</strong><em>周一至周五 9:00-18:00</em></div>
  <div class="certs"><i></i><i></i><i></i><i></i><i></i><i></i></div>
</footer>

<div class="copyright">
  <span>Copyright © 2014 京ICP备00000000号 版权所有 | 北京可路网络科技有限公司</span>
  <div class="brand"><span class="brand-dot"></span>可路贷</div>
</div>
</body>
</html>
```